Kestrel Facilities Business Card Design

We would now like to design business cards with the new Kestrel Facilities logo

Target Market(s)

Professional

Industry/Entity Type

Professional services

Contact Information for Business Card

Employee name, title, phone number, email address, corporate office address and logo.

Font styles to use
Sans Serif

Colors
0054AA
0677BA
7BADD7
CADEEF
E8F1F8

Requirements
Must have
• My logo
Should not have
• any other pictures or images besides my logo

```html
<!DOCTYPE html>
<html lang="en">
<head>
<meta charset="utf-8">
<title>Kestrel Facilities Business Card</title>
<link href="https://fonts.googleapis.com/css2?family=Montserrat:wght@400;500;700;800&display=swap" rel="stylesheet">
<style>
  :root {
    --brand-blue: #3375bd;
    --deep-blue: #0054aa;
    --logo-light: #cfd6e6;
    --stripe-grey: #b3b3b8;
    --ink: #1d1d1f;
    --paper: #ffffff;
    --backdrop: #e6e8ec;
  }
  * { margin: 0; padding: 0; box-sizing: border-box; }
  html, body { width: 1200px; height: 960px; overflow: hidden; }
  body {
    background: var(--backdrop);
    font-family: "Montserrat", sans-serif;
    display: flex;
    flex-direction: column;
    align-items: center;
    justify-content: center;
    gap: 56px;
  }
  .card {
    position: relative;
    width: 640px;
    height: 366px;
    border-radius: 22px;
    overflow: hidden;
    box-shadow: 0 10px 26px rgba(0,0,0,0.18);
  }
  .card-back {
    background: var(--brand-blue);
    display: flex;
    align-items: center;
    justify-content: center;
  }
  .wordmark {
    display: flex;
    align-items: center;
    gap: 16px;
    font-weight: 700;
    letter-spacing: 0.02em;
    line-height: 1.05;
  }
  .wordmark-square { width: 54px; height: 54px; }
  .card-back .wordmark { color: var(--logo-light); font-size: 40px; }
  .card-back .wordmark-square { background: var(--logo-light); width: 66px; height: 66px; }
  .card-front { background: var(--paper); }
  .front-wave { position: absolute; left: 0; bottom: 0; width: 100%; height: 190px; }
  .front-logo {
    position: absolute;
    left: 54px;
    top: 102px;
  }
  .card-front .wordmark { color: var(--brand-blue); font-size: 31px; }
  .card-front .wordmark-square { background: var(--brand-blue); }
  .divider {
    position: absolute;
    left: 330px;
    top: 56px;
    width: 2px;
    height: 180px;
    background: var(--brand-blue);
  }
  .contact {
    position: absolute;
    left: 356px;
    top: 44px;
    color: var(--ink);
    font-size: 14px;
    line-height: 1.35;
  }
  .person-name { color: var(--brand-blue); font-weight: 800; font-size: 22px; letter-spacing: 0.01em; }
  .person-title { font-size: 15px; margin-bottom: 14px; }
  .address { margin-bottom: 12px; }
  .contact-line { display: flex; align-items: center; gap: 8px; font-size: 14px; }
  .contact-line svg { width: 14px; height: 14px; flex: none; }
</style>
</head>
<body>
  <section class="card card-back" aria-label="Business card back">
    <div class="wordmark">
      <span class="wordmark-square"></span>
      <span>Kestrel<br>Facilities</span>
    </div>
  </section>

  <section class="card card-front" aria-label="Business card front">
    <svg class="front-wave" viewBox="0 0 640 190" preserveAspectRatio="none">
      <path d="M0 176 C180 170 260 120 360 80 C460 40 560 16 640 8 L640 20 C560 28 460 54 360 94 C260 134 180 184 0 190 Z" fill="var(--stripe-grey)"/>
      <path d="M0 190 C180 184 260 134 360 94 C460 54 560 28 640 20 L640 190 Z" fill="var(--brand-blue)"/>
    </svg>

    <div class="front-logo">
      <div class="wordmark">
        <span class="wordmark-square"></span>
        <span>Kestrel<br>Facilities</span>
      </div>
    </div>

    <div class="divider"></div>

    <div class="contact">
      <p class="person-name">DARIN HOLLOWAY</p>
      <p class="person-title">Co-Founder</p>
      <p class="address">4180 N. Harbor Lane<br>Suite 1204 Westfield.31</p>
      <p class="contact-line">
        <svg viewBox="0 0 16 16"><path d="M3 2l3 0 1 4-2 1c1 2 2 3 4 4l1-2 4 1 0 3c-6 1-12-5-11-11z" fill="var(--brand-blue)"/></svg>
        +254-155-01234
      </p>
      <p class="contact-line">
        <svg viewBox="0 0 16 16"><rect x="1" y="3" width="14" height="10" fill="var(--brand-blue)"/><path d="M1 3l7 6 7-6" stroke="#fff" stroke-width="1.4" fill="none"/></svg>
        info@kestrelfm.com
      </p>
      <p class="contact-line">
        <svg viewBox="0 0 16 16"><circle cx="8" cy="8" r="7" fill="var(--brand-blue)"/><path d="M1 8h14M8 1c-3 4-3 10 0 14M8 1c3 4 3 10 0 14" stroke="#fff" stroke-width="1" fill="none"/></svg>
        www.kestrelfm.com
      </p>
    </div>
  </section>
</body>
</html>
```